DuePath.com website design

We are a collection agency that collects debt from past residents of apartments on behalf of Property Management Companies. We are want to design a 3 page website with - Home - How it Works - Schedule Demo. We'd like a sketch of a skyline showing high rise apartment buildings, houses, shops, etc. We would like for there to be some animation, possibly clouds and the sun slowly moving. Maybe kids playing ball or catch or something like that. Bird flying and landing. An electric car charging (to indicate we are modern). We are looking for a friendly community vibe. The site will also need a button "Property Managers Login". When some comes to the site we would like a pop up that says "Property Managers Click Here/Past Residents Click Here" with a different icon for each that relates to the description. I've included a link to a test site we had designed so feel free to use some of the copy from it. We just aren't happy with the design. On the Home page our tag line should be "Get more payments, faster, from past residents!" and "Digital First, NOT Digital Only". All without transaction fees, we don't get paid unless we get you paid first!
Additional selling points:

24 hour virtual agent and virtual telephone agent so we don't miss any opportunities to GET YOUR MONEY!

Old school collection strategies meet cutting edge technology to create effective work flow algorithms to put the best debt collectors on your accounts with data driven intelligence to determine the best way to get paid.

No Subscription Fees
No Payment Processing Fees
No Software Fees
No Mail, Email or TXT Fees

Inquire about our FIRST PARTY accounts receivable outsourcing. You may qualify for free post move out A/R processing and AI payment negotiator for the low hanging fruit. Don't pay full collection commission when there wasn't a full collection attempt!

For the How it Works page - See the page from our previous design. I will include the link below. Please come up with your own version of this but you can use the copy from this page.

The schedule demo page will be a form that will feed to our CRM that will include:
Name
Email
Company
Title
Phone Number
Number of Units
Tell us how we can help you: (a box for them provide details)

Also include our phone number at the bottom with something like

Here is a link to our previous design test site:
https://brookpreview.net/duepath-new/
I've attached an image of the back end so you can get an idea of the colors we need, I've also included our logo. For the most part we would like most of the site to match the blue colors from our logo, but we do need to incorporate some of the yellow in the images I've attached. Possibly make the buttons on the site the yellow color? Make the sun Match the yellow? I'll leave it up to you.

```html
<!DOCTYPE html>
<html lang="en">
<head>
<meta charset="utf-8">
<title>DuePath.com – Home page design</title>
<link rel="stylesheet" href="https://fonts.googleapis.com/css2?family=Yanone+Kaffeesatz:wght@400;500;600&family=Open+Sans:wght@400;600;700&display=swap">
<style>
  :root{
    --stage:#e9e9e9;
    --teal:#2bbccd;
    --teal-bar:#2ab6ca;
    --navy:#16386b;
    --ink:#2f3136;
    --white:#ffffff;
    --yellow:#ffea00;
    --card:#f6f6f6;
    --red:#e0262b;
    --sky-top:#c9ecfa;
    --sky-low:#9fd2f3;
    --shade:rgba(14,24,34,.62);
    --head:"Yanone Kaffeesatz",sans-serif;
    --body:"Open Sans",sans-serif;
  }
  *{box-sizing:border-box;margin:0;padding:0}
  html,body{width:1134px;height:1200px;overflow:hidden;background:var(--stage)}
  body{position:relative;font-family:var(--body);color:var(--ink)}

  .page{position:absolute;top:52px;width:532px;height:1091px;background:var(--white);overflow:hidden}
  .page--popup{left:24px}
  .page--plain{left:575px}

  .topbar{height:15px;background:var(--teal-bar);color:var(--white);font-size:6.2px;font-weight:700;
    display:flex;align-items:center;justify-content:center;letter-spacing:.01em}
  .topbar em{font-style:normal;color:var(--yellow)}

  .nav{height:43px;position:relative;background:var(--white)}
  .brand{position:absolute;left:64px;top:13px;display:flex;align-items:center;gap:4px}
  .brand__mark{width:15px;height:15px;border-radius:3px;background:var(--teal)}
  .brand__name{font-family:var(--body);font-weight:700;font-size:12px;color:var(--navy);letter-spacing:-.01em}
  .nav__link{position:absolute;top:16px;font-size:8px;color:var(--ink)}
  .nav__link--home{left:246px}
  .nav__link--how{left:286px}
  .nav__active{position:absolute;left:239px;bottom:0;width:37px;height:3px;background:var(--teal)}
  .nav__cta{position:absolute;top:0;height:43px;background:var(--yellow);color:var(--ink);
    display:flex;align-items:center;justify-content:center;text-align:center;line-height:1.2}
  .nav__cta--demo{left:351px;width:53px;font-size:7.8px}
  .nav__cta--login{left:415px;width:53px;font-size:9px;font-weight:700}

  .hero{height:245px;position:relative}
  .hero__scene{position:absolute;inset:0;background:linear-gradient(180deg,var(--sky-top) 0%,var(--sky-top) 40%,var(--sky-low) 100%)}
  .hero__title{position:absolute;top:22px;left:0;right:0;text-align:center;font-family:var(--head);
    font-weight:500;font-size:23px;line-height:25px;color:var(--navy)}
  .hero__cta{position:absolute;top:84px;left:236px;width:59px;height:16px;background:var(--yellow);
    font-size:7px;font-weight:700;display:flex;align-items:center;justify-content:center;border-radius:2px}

  .btn{display:flex;align-items:center;justify-content:center;width:59px;height:19px;background:var(--yellow);
    color:var(--ink);font-size:7px;font-weight:700;border-radius:2px}

  .about{height:130px;background:var(--teal);position:relative;color:var(--white)}
  .about__name{position:absolute;left:40px;top:48px;font-weight:700;font-size:22px;color:var(--white)}
  .about__body{position:absolute;left:170px;top:16px;width:300px}
  .about__title{font-family:var(--head);font-weight:500;font-size:25px;line-height:1}
  .about__text{margin-top:8px;font-size:7.2px;line-height:12px}
  .about .btn{margin-top:11px}

  .benefits{height:255px;text-align:center;position:relative}
  .section-title{font-family:var(--head);font-weight:500;font-size:27px;line-height:1}
  .benefits .section-title{padding-top:20px;color:var(--navy)}
  .benefits__lead,.benefits__note{width:400px;margin:7px auto 0;font-size:6.8px;line-height:12px;color:var(--ink)}
  .benefit-grid{display:flex;gap:8px;justify-content:center;margin-top:13px}
  .benefit{width:94px;height:73px;background:var(--card);border-radius:4px;display:flex;flex-direction:column;
    align-items:center;padding-top:10px}
  .benefit svg{width:44px;height:34px}
  .benefit__label{margin-top:5px;font-family:var(--head);font-size:9.5px;color:var(--navy)}
  .benefits__note{margin-top:16px}
  .benefits .btn{margin:10px auto 0}

  .services{height:250px;background:var(--teal);text-align:center;color:var(--white);position:relative}
  .services .section-title{padding-top:16px}
  .service-row{display:flex;justify-content:center;gap:43px;margin-top:8px}
  .service{width:106px;display:flex;flex-direction:column;align-items:center}
  .service__disc{width:106px;height:106px;border-radius:50%;background:var(--white);display:flex;flex-direction:column;
    align-items:center;justify-content:center;color:var(--navy)}
  .service__disc svg{width:28px;height:28px;margin-bottom:6px}
  .service__name{font-family:var(--head);font-size:12px;line-height:12px}
  .service__text{margin-top:15px;width:104px;font-size:7px;line-height:12px}
  .service .btn{margin-top:6px}

  .footer{height:153px;position:relative;background:var(--white)}
  .social{position:absolute;top:17px;left:227px;display:flex;gap:16px}
  .social span{width:13px;height:13px;border-radius:50%;background:#1d96d2}
  .footer__brand{position:absolute;left:72px;top:53px;display:flex;align-items:center;gap:6px}
  .footer__brand .brand__mark{width:26px;height:26px;border-radius:5px}
  .footer__brand .brand__name{font-size:22px}
  .footer__about{position:absolute;left:244px;top:48px;width:226px;font-size:7.2px;line-height:12px;color:var(--ink)}
  .footer__links{position:absolute;top:100px;left:0;width:100%;font-size:9px;color:#1d4f8f}
  .footer__links span{position:absolute}
  .footer__rule{position:absolute;top:121px;left:0;right:0;height:1px;background:#e3e3e3}
  .footer__copy{position:absolute;top:132px;left:0;right:0;text-align:center;font-size:5.5px;color:var(--ink)}

  .shade{position:absolute;inset:0;background:var(--shade);z-index:5}
  .entry-modal{position:absolute;left:80px;top:146px;width:357px;height:142px;background:var(--teal);
    border-radius:3px;z-index:6}
  .entry-modal__close{position:absolute;left:340px;top:6px;color:var(--white);font-size:9px}
  .entry-card{position:absolute;top:30px;width:104px;height:77px;background:var(--yellow);border-radius:3px;
    display:flex;flex-direction:column;align-items:center;padding-top:8px;color:var(--navy)}
  .entry-card--managers{left:54px}
  .entry-card--residents{left:186px}
  .entry-card svg{width:30px;height:30px}
  .entry-card__label{font-family:var(--head);font-size:12.5px;line-height:15px;text-align:center;margin-top:3px}
</style>
</head>
<body>

<!-- Home page with entry pop-up open -->
<section class="page page--popup" aria-label="Home page with visitor pop-up">
  <div class="topbar">24 hour virtual agent and virtual telephone agent so we don't miss any opportunities to&nbsp;<em>GET YOUR MONEY!</em></div>
  <header class="nav">
    <div class="brand"><span class="brand__mark"></span><span class="brand__name">DuePath</span></div>
    <span class="nav__link nav__link--home">Home</span>
    <span class="nav__link nav__link--how">How it Works</span>
    <span class="nav__active"></span>
    <span class="nav__cta nav__cta--demo">Schedule<br>Demo</span>
    <span class="nav__cta nav__cta--login">Login</span>
  </header>
  <div class="hero">
    <div class="hero__scene" role="img" aria-label="Illustration of a sunny city skyline with apartment towers, clouds, birds, an electric car charging and families walking and cycling"></div>
    <h1 class="hero__title">Get More Payments,<br>Faster, From Past Residents!</h1>
    <span class="hero__cta">Schedule Now</span>
  </div>
  <section class="about">
    <span class="about__name">DuePath</span>
    <div class="about__body">
      <h2 class="about__title">About Us</h2>
      <p class="about__text">Old school collection strategies meet cutting edge technology to create effective work flow algorithms to put the best debt collectors on your accounts with data driven intelligence to determine the best way to get paid.</p>
      <span class="btn">Read More</span>
    </div>
  </section>
  <section class="benefits">
    <h2 class="section-title">Benefits</h2>
    <p class="benefits__lead">Old school collection strategies meet cutting edge technology to create effective work flow algorithms to put the best debt collectors on your accounts with data driven intelligence to determine the best way to get paid.</p>
    <div class="benefit-grid">
      <div class="benefit"><svg viewBox="0 0 44 34" fill="none" stroke="#16386b" stroke-width="1.4"><rect x="14" y="3" width="24" height="18" rx="1"/><line x1="14" y1="8" x2="38" y2="8"/><path d="M28 16v12l3-2 2 5"/><circle cx="10" cy="23" r="7" stroke="#e0262b" stroke-width="1.8"/><line x1="5" y1="28" x2="15" y2="18" stroke="#e0262b" stroke-width="1.8"/></svg><span class="benefit__label">No Subscription Fees</span></div>
      <div class="benefit"><svg viewBox="0 0 44 34" fill="none" stroke="#16386b" stroke-width="1.4"><circle cx="27" cy="14" r="10"/><path d="M27 8v12M24 11h5M24 17h5"/><circle cx="12" cy="22" r="7" stroke="#e0262b" stroke-width="1.8"/><line x1="7" y1="27" x2="17" y2="17" stroke="#e0262b" stroke-width="1.8"/></svg><span class="benefit__label">No Payment Processing Fees</span></div>
      <div class="benefit"><svg viewBox="0 0 44 34" fill="none" stroke="#16386b" stroke-width="1.4"><rect x="15" y="4" width="24" height="17" rx="1"/><line x1="27" y1="21" x2="27" y2="27"/><line x1="21" y1="27" x2="33" y2="27"/><rect x="23" y="9" width="8" height="7"/><circle cx="11" cy="22" r="7" stroke="#e0262b" stroke-width="1.8"/><line x1="6" y1="27" x2="16" y2="17" stroke="#e0262b" stroke-width="1.8"/></svg><span class="benefit__label">No Software Fees</span></div>
      <div class="benefit"><svg viewBox="0 0 44 34" fill="none" stroke="#16386b" stroke-width="1.4"><rect x="15" y="11" width="20" height="14" rx="1"/><path d="M15 11l10 8 10-8"/><circle cx="33" cy="9" r="6"/><line x1="29" y1="13" x2="37" y2="5"/><circle cx="11" cy="23" r="7" stroke="#e0262b" stroke-width="1.8"/><line x1="6" y1="28" x2="16" y2="18" stroke="#e0262b" stroke-width="1.8"/></svg><span class="benefit__label">No Mail, Email or TXT Fees</span></div>
    </div>
    <p class="benefits__note">Inquire about our FIRST PARTY accounts receivable outsourcing. You may qualify for free post move out A/R processing and AI payment negotiator for the low hanging fruit. Don't pay full collection commission when there wasn't a full collection attempt!</p>
    <span class="btn">Read More</span>
  </section>
  <section class="services">
    <h2 class="section-title">Services</h2>
    <div class="service-row">
      <div class="service"><div class="service__disc"><svg viewBox="0 0 28 28" fill="none" stroke="#16386b" stroke-width="1.6"><rect x="4" y="6" width="10" height="20"/><rect x="14" y="12" width="10" height="14" fill="#2bbccd"/><line x1="2" y1="26" x2="26" y2="26"/></svg><span class="service__name">Property Management<br>Debt Experts</span></div><p class="service__text">DuePath exclusively serves the apartment and student housing industries.</p><span class="btn">Read More</span></div>
      <div class="service"><div class="service__disc"><svg viewBox="0 0 28 28" fill="none" stroke="#16386b" stroke-width="1.6"><rect x="5" y="3" width="18" height="10" rx="1"/><circle cx="14" cy="8" r="2.5"/><path d="M3 22h7l6-4h7v6H3z" fill="#2bbccd"/></svg><span class="service__name">We Make It Easy To Pay</span></div><p class="service__text">Our technology gives past residents multiple payment platforms.</p><span class="btn">Read More</span></div>
      <div class="service"><div class="service__disc"><svg viewBox="0 0 28 28" fill="none" stroke="#16386b" stroke-width="1.8"><path d="M6 22l5-5M17 11l5-5"/><rect x="9" y="13" width="6" height="10" rx="3" transform="rotate(45 12 18)" fill="#2bbccd"/><rect x="13" y="5" width="6" height="10" rx="3" transform="rotate(45 16 10)"/></svg><span class="service__name">Break The Cycle</span></div><p class="service__text">Stop using old-school collection agencies that put you at financial and reputational risk.</p><span class="btn">Read More</span></div>
    </div>
  </section>
  <footer class="footer">
    <div class="social"><span></span><span></span><span></span></div>
    <div class="footer__brand"><span class="brand__mark"></span><span class="brand__name">DuePath</span></div>
    <p class="footer__about">Lorem Ipsum is simply dummy text of the printing and typesetting industry. Lorem Ipsum has been the industry's standard dummy text ever since the 1500s.</p>
    <nav class="footer__links"><span style="left:155px">Home</span><span style="left:203px">How it Works</span><span style="left:277px">About Us</span><span style="left:337px">Contact Us</span></nav>
    <div class="footer__rule"></div>
    <p class="footer__copy">© copyrights 2022 DuePath | &nbsp;All Rights Reserved</p>
  </footer>

  <div class="shade"></div>
  <div class="entry-modal" role="dialog" aria-label="Choose your visitor type">
    <span class="entry-modal__close">X</span>
    <div class="entry-card entry-card--managers">
      <svg viewBox="0 0 30 30" fill="none" stroke="#16386b" stroke-width="1.5"><rect x="5" y="9" width="12" height="18"/><rect x="17" y="14" width="9" height="13" fill="#2bbccd"/><line x1="9" y1="14" x2="13" y2="14"/><line x1="9" y1="19" x2="13" y2="19"/><line x1="3" y1="27" x2="28" y2="27"/></svg>
      <span class="entry-card__label">Property<br>Managers</span>
    </div>
    <div class="entry-card entry-card--residents">
      <svg viewBox="0 0 30 30" fill="none" stroke="#16386b" stroke-width="1.5"><path d="M3 14L15 4l12 10"/><path d="M6 12v15h18V12"/><rect x="12" y="18" width="6" height="9" fill="#2bbccd"/></svg>
      <span class="entry-card__label">Past<br>Residents</span>
    </div>
  </div>
</section>

<!-- Home page -->
<section class="page page--plain" aria-label="Home page">
  <div class="topbar">24 hour virtual agent and virtual telephone agent so we don't miss any opportunities to&nbsp;<em>GET YOUR MONEY!</em></div>
  <header class="nav">
    <div class="brand"><span class="brand__mark"></span><span class="brand__name">DuePath</span></div>
    <span class="nav__link nav__link--home">Home</span>
    <span class="nav__link nav__link--how">How it Works</span>
    <span class="nav__active"></span>
    <span class="nav__cta nav__cta--demo">Schedule<br>Demo</span>
    <span class="nav__cta nav__cta--login">Login</span>
  </header>
  <div class="hero">
    <div class="hero__scene" role="img" aria-label="Illustration of a sunny city skyline with apartment towers, clouds, birds, an electric car charging and families walking and cycling"></div>
    <h1 class="hero__title">Get More Payments,<br>Faster, From Past Residents!</h1>
    <span class="hero__cta">Schedule Now</span>
  </div>
  <section class="about">
    <span class="about__name">DuePath</span>
    <div class="about__body">
      <h2 class="about__title">About Us</h2>
      <p class="about__text">Old school collection strategies meet cutting edge technology to create effective work flow algorithms to put the best debt collectors on your accounts with data driven intelligence to determine the best way to get paid.</p>
      <span class="btn">Read More</span>
    </div>
  </section>
  <section class="benefits">
    <h2 class="section-title">Benefits</h2>
    <p class="benefits__lead">Old school collection strategies meet cutting edge technology to create effective work flow algorithms to put the best debt collectors on your accounts with data driven intelligence to determine the best way to get paid.</p>
    <div class="benefit-grid">
      <div class="benefit"><svg viewBox="0 0 44 34" fill="none" stroke="#16386b" stroke-width="1.4"><rect x="14" y="3" width="24" height="18" rx="1"/><line x1="14" y1="8" x2="38" y2="8"/><path d="M28 16v12l3-2 2 5"/><circle cx="10" cy="23" r="7" stroke="#e0262b" stroke-width="1.8"/><line x1="5" y1="28" x2="15" y2="18" stroke="#e0262b" stroke-width="1.8"/></svg><span class="benefit__label">No Subscription Fees</span></div>
      <div class="benefit"><svg viewBox="0 0 44 34" fill="none" stroke="#16386b" stroke-width="1.4"><circle cx="27" cy="14" r="10"/><path d="M27 8v12M24 11h5M24 17h5"/><circle cx="12" cy="22" r="7" stroke="#e0262b" stroke-width="1.8"/><line x1="7" y1="27" x2="17" y2="17" stroke="#e0262b" stroke-width="1.8"/></svg><span class="benefit__label">No Payment Processing Fees</span></div>
      <div class="benefit"><svg viewBox="0 0 44 34" fill="none" stroke="#16386b" stroke-width="1.4"><rect x="15" y="4" width="24" height="17" rx="1"/><line x1="27" y1="21" x2="27" y2="27"/><line x1="21" y1="27" x2="33" y2="27"/><rect x="23" y="9" width="8" height="7"/><circle cx="11" cy="22" r="7" stroke="#e0262b" stroke-width="1.8"/><line x1="6" y1="27" x2="16" y2="17" stroke="#e0262b" stroke-width="1.8"/></svg><span class="benefit__label">No Software Fees</span></div>
      <div class="benefit"><svg viewBox="0 0 44 34" fill="none" stroke="#16386b" stroke-width="1.4"><rect x="15" y="11" width="20" height="14" rx="1"/><path d="M15 11l10 8 10-8"/><circle cx="33" cy="9" r="6"/><line x1="29" y1="13" x2="37" y2="5"/><circle cx="11" cy="23" r="7" stroke="#e0262b" stroke-width="1.8"/><line x1="6" y1="28" x2="16" y2="18" stroke="#e0262b" stroke-width="1.8"/></svg><span class="benefit__label">No Mail, Email or TXT Fees</span></div>
    </div>
    <p class="benefits__note">Inquire about our FIRST PARTY accounts receivable outsourcing. You may qualify for free post move out A/R processing and AI payment negotiator for the low hanging fruit. Don't pay full collection commission when there wasn't a full collection attempt!</p>
    <span class="btn">Read More</span>
  </section>
  <section class="services">
    <h2 class="section-title">Services</h2>
    <div class="service-row">
      <div class="service"><div class="service__disc"><svg viewBox="0 0 28 28" fill="none" stroke="#16386b" stroke-width="1.6"><rect x="4" y="6" width="10" height="20"/><rect x="14" y="12" width="10" height="14" fill="#2bbccd"/><line x1="2" y1="26" x2="26" y2="26"/></svg><span class="service__name">Property Management<br>Debt Experts</span></div><p class="service__text">DuePath exclusively serves the apartment and student housing industries.</p><span class="btn">Read More</span></div>
      <div class="service"><div class="service__disc"><svg viewBox="0 0 28 28" fill="none" stroke="#16386b" stroke-width="1.6"><rect x="5" y="3" width="18" height="10" rx="1"/><circle cx="14" cy="8" r="2.5"/><path d="M3 22h7l6-4h7v6H3z" fill="#2bbccd"/></svg><span class="service__name">We Make It Easy To Pay</span></div><p class="service__text">Our technology gives past residents multiple payment platforms.</p><span class="btn">Read More</span></div>
      <div class="service"><div class="service__disc"><svg viewBox="0 0 28 28" fill="none" stroke="#16386b" stroke-width="1.8"><path d="M6 22l5-5M17 11l5-5"/><rect x="9" y="13" width="6" height="10" rx="3" transform="rotate(45 12 18)" fill="#2bbccd"/><rect x="13" y="5" width="6" height="10" rx="3" transform="rotate(45 16 10)"/></svg><span class="service__name">Break The Cycle</span></div><p class="service__text">Stop using old-school collection agencies that put you at financial and reputational risk.</p><span class="btn">Read More</span></div>
    </div>
  </section>
  <footer class="footer">
    <div class="social"><span></span><span></span><span></span></div>
    <div class="footer__brand"><span class="brand__mark"></span><span class="brand__name">DuePath</span></div>
    <p class="footer__about">Lorem Ipsum is simply dummy text of the printing and typesetting industry. Lorem Ipsum has been the industry's standard dummy text ever since the 1500s.</p>
    <nav class="footer__links"><span style="left:155px">Home</span><span style="left:203px">How it Works</span><span style="left:277px">About Us</span><span style="left:337px">Contact Us</span></nav>
    <div class="footer__rule"></div>
    <p class="footer__copy">© copyrights 2022 DuePath | &nbsp;All Rights Reserved</p>
  </footer>
</section>

</body>
</html>
```